Executive Business Card for Healthcare Company [Need Today]

I need a business card design for a healthcare company. The only branding the company has thus far is a logo. The cards will be utilized by company executives. The design I envision will be vibrant and appealing but with a corporate feel. They shouldn't be too casual or playful. I would like to complete this project TODAY if possible.

Target Market(s)

Healthcare vendors, other executives in healthcare and pharmaceuticals

Industry/Entity Type

Pharmaceutical

Contact Information for Business Card

See attachment

Font styles to use
Serif
Sans Serif

Colors

Designer to choose colors to be used in the design.

```html
<!DOCTYPE html>
<html lang="en">
<head>
<meta charset="utf-8">
<title>Tessaly Therapeutics — Business Card</title>
<link href="https://fonts.googleapis.com/css2?family=Raleway:wght@300;400&family=Roboto:wght@300;400;500&display=swap" rel="stylesheet">
<style>
  :root{
    --bg:#e6e7e8;
    --teal:#27b1c2;
    --green:#4fb48c;
    --teal-dark:#1f8f9a;
    --ink:#2fa6b3;
    --text:#4a4d50;
    --muted:#8a8d90;
    --paper:#ffffff;
    --rule:#9ea1a4;
  }
  *{margin:0;padding:0;box-sizing:border-box}
  html,body{width:1200px;height:726px;overflow:hidden;background:var(--bg)}
  .canvas{
    width:1200px;height:726px;display:flex;align-items:center;justify-content:center;gap:36px;
    font-family:"Roboto",sans-serif;
  }
  .card{
    position:relative;width:560px;height:320px;overflow:hidden;
    box-shadow:0 6px 18px rgba(0,0,0,.12);
  }
  /* Front */
  .card--front{
    background:linear-gradient(180deg,var(--teal) 0%,var(--green) 100%);
    color:var(--paper);
  }
  .front-brand{position:absolute;left:0;right:0;top:104px;text-align:center}
  .brand-name{
    font-family:"Raleway",sans-serif;font-weight:300;font-size:62px;letter-spacing:1px;line-height:1;
  }
  .brand-sub{
    font-family:"Raleway",sans-serif;font-weight:300;font-size:26px;letter-spacing:1px;margin-top:4px;
  }
  .front-web{
    position:absolute;left:0;right:0;bottom:40px;text-align:center;
    font-family:"Raleway",sans-serif;font-weight:400;font-size:14px;letter-spacing:4px;
  }
  /* Back */
  .card--back{background:var(--paper);color:var(--text)}
  .back-band{
    position:absolute;left:0;top:0;bottom:0;width:44px;
    background:linear-gradient(180deg,var(--teal-dark) 0%,var(--green) 100%);
  }
  .back-band::after{
    content:"";position:absolute;right:-8px;top:0;bottom:0;width:8px;background:var(--rule);
  }
  .logo{
    position:absolute;left:92px;top:40px;display:flex;align-items:center;gap:14px;
  }
  .logo-dot{width:62px;height:62px;border-radius:50%;border:3px solid var(--ink)}
  .logo-divider{width:1px;height:54px;background:var(--rule)}
  .logo-text{color:var(--ink)}
  .logo-text .brand-name{font-size:40px}
  .logo-text .brand-sub{font-size:17px;margin-top:0}
  .person{position:absolute;left:92px;top:142px}
  .person-name{font-family:"Raleway",sans-serif;font-weight:400;font-size:25px;color:var(--ink)}
  .person-title{font-size:12px;color:var(--muted);margin-top:4px;margin-left:18px}
  .contact{position:absolute;left:92px;top:210px;list-style:none;font-size:15px;font-weight:300}
  .contact li{display:flex;align-items:center;gap:10px;height:22px}
  .contact svg{width:14px;height:14px;fill:var(--text);flex:none}
  .contact .accent{color:var(--ink)}
  .contact .address{margin-top:2px}
</style>
</head>
<body>
<main class="canvas">
  <section class="card card--front" aria-label="Card front">
    <div class="front-brand">
      <div class="brand-name">tessaly</div>
      <div class="brand-sub">therapeutics</div>
    </div>
    <div class="front-web">www.tessalyrx.com</div>
  </section>

  <section class="card card--back" aria-label="Card back">
    <div class="back-band"></div>
    <div class="logo">
      <div class="logo-dot"></div>
      <div class="logo-divider"></div>
      <div class="logo-text">
        <div class="brand-name">tessaly</div>
        <div class="brand-sub">therapeutics</div>
      </div>
    </div>
    <div class="person">
      <div class="person-name">Marcus Hale</div>
      <div class="person-title">Senior Director of Marketing</div>
    </div>
    <ul class="contact">
      <li><svg viewBox="0 0 24 24"><path d="M6.6 10.8a15 15 0 0 0 6.6 6.6l2.2-2.2a1 1 0 0 1 1-.25 11.4 11.4 0 0 0 3.6.57 1 1 0 0 1 1 1V20a1 1 0 0 1-1 1A17 17 0 0 1 3 4a1 1 0 0 1 1-1h3.5a1 1 0 0 1 1 1c0 1.25.2 2.45.57 3.57a1 1 0 0 1-.25 1z"/></svg><span>555-201-4836</span></li>
      <li><svg viewBox="0 0 24 24"><path d="M7 1h10a2 2 0 0 1 2 2v18a2 2 0 0 1-2 2H7a2 2 0 0 1-2-2V3a2 2 0 0 1 2-2zm0 3v14h10V4zm5 15.5a1 1 0 1 0 0 2 1 1 0 0 0 0-2z"/></svg><span>555-307-6142</span></li>
      <li><svg viewBox="0 0 24 24"><path d="M12 2a10 10 0 1 0 0 20 10 10 0 0 0 0-20zm6.9 6h-3a15 15 0 0 0-1.3-3.9A8 8 0 0 1 18.9 8zM12 4c.8 1.2 1.5 2.5 1.9 4h-3.8c.4-1.5 1.1-2.8 1.9-4zM4.3 14a8 8 0 0 1 0-4h3.4a16 16 0 0 0 0 4zm.8 2h3a15 15 0 0 0 1.3 3.9A8 8 0 0 1 5.1 16zm3-8h-3a8 8 0 0 1 4.3-3.9C8.8 5.3 8.4 6.6 8.1 8zM12 20c-.8-1.2-1.5-2.5-1.9-4h3.8c-.4 1.5-1.1 2.8-1.9 4zm2.3-6H9.7a14 14 0 0 1 0-4h4.6a14 14 0 0 1 0 4zm.3 5.9a15 15 0 0 0 1.3-3.9h3a8 8 0 0 1-4.3 3.9zm1.7-5.9a16 16 0 0 0 0-4h3.4a8 8 0 0 1 0 4z"/></svg><span>mhale@<span class="accent">tessalyrx</span>.com</span></li>
      <li class="address"><span>118 W Maple Avenue Dalton, GA 30720</span></li>
    </ul>
  </section>
</main>
</body>
</html>
```